bRIDGE ON LLC - New Website Design Help!

Need to build a website that showcases our capabilities. We will be specializing in Government Contracting for SDVOSB set aside and sole source contracts. We provide many services such as Audio & Visual design, install, consulting, all the way through to project completion. Also, IT/Voice infrastructure consulting, design, implementation, project management all the way to project completion.

Target Market(s)

IT/Voice Government Contracts, Managed Service Contracts for Government

Industry/Entity Type

Information Technology and Telecommunications

Coding

Coded - Design and coding required

Number of Pages Required

5+ page

Font styles to use
Other font styles liked:
• Calibri

Colors

Designer to choose only greyscale colors for use in the design.

Requirements
Must have
• Drop downs for additional pages, for About Us, Services, Industry Solutions, Our Company, Contact Us
Nice to have
• Testimonials page or Blog page

```html
<!DOCTYPE html>
<html lang="en">
<head>
<meta charset="utf-8">
<title>bRIDGE ON LLC</title>
<link href="https://fonts.googleapis.com/css2?family=Lato:wght@400;700;900&display=swap" rel="stylesheet">
<style>
:root{
  --ink:#1e1e1e;
  --dark:#2b2b2b;
  --card-dark:#2f2f2f;
  --mid:#3d3d3d;
  --grey:#6b6b6b;
  --soft:#f2f1f2;
  --line:#dedede;
  --nav:#e6e6e6;
  --white:#ffffff;
  --black:#0d0d0d;
}
*{box-sizing:border-box;margin:0;padding:0}
html,body{width:1200px;height:5286px;overflow:hidden}
body{font-family:'Lato',sans-serif;color:var(--ink);background:var(--white);position:relative}
.abs{position:absolute}
.brand{font-weight:900;font-size:34px;letter-spacing:1px;color:var(--ink);display:flex;align-items:center;gap:10px}
.brand .sq{width:18px;height:18px;background:var(--ink)}
.topbar{left:0;top:0;width:1200px;height:92px}
.contact-chip{display:flex;align-items:center;gap:14px;font-size:19px;color:var(--ink)}
.chip-ic{width:48px;height:48px;border-radius:50%;border:2px solid var(--ink);display:flex;align-items:center;justify-content:center}
.nav{left:0;top:92px;width:1200px;height:56px;background:var(--nav);display:flex;align-items:center;padding-left:92px;gap:56px;font-size:13px;font-weight:700;letter-spacing:.4px}
.hero{left:0;top:148px;width:1200px;height:660px;background:linear-gradient(100deg,#3a1d1d 0%,#5c3a22 30%,#2a2f3a 60%,#514a2c 85%,#2b2b2b 100%)}
.hero-shade{left:0;top:148px;width:1200px;height:660px;background:linear-gradient(90deg,rgba(0,0,0,.55),rgba(0,0,0,.1))}
.hero h1{left:75px;top:330px;font-size:90px;font-weight:900;color:var(--white);letter-spacing:1px}
.hero-text{left:75px;top:430px;width:620px;font-size:23px;line-height:32px;color:var(--white)}
.btn{display:inline-flex;align-items:center;justify-content:center;border-radius:30px;font-weight:700;color:var(--white);background:var(--mid)}
.btn-hero{left:75px;top:525px;width:182px;height:50px;background:var(--ink);font-size:19px}
h2.sec{font-size:42px;font-weight:900;color:var(--ink);letter-spacing:.3px}
.svc-card{background:var(--white);box-shadow:0 4px 14px rgba(0,0,0,.18);padding:22px 16px}
.svc-card h3{font-size:17px;font-weight:700;margin:14px 0 10px}
.svc-card p{font-size:13px;line-height:23px;color:var(--grey)}
.btn-sm{height:40px;padding:0 18px;font-size:13px;margin-top:16px;margin-left:-16px;border-radius:0 22px 22px 0}
.body-text{font-size:15px;line-height:32px;color:var(--grey)}
.photo{border-radius:34px}
.ind-card{background:var(--card-dark);color:var(--white);text-align:center;padding:20px 18px;box-shadow:0 4px 12px rgba(0,0,0,.3)}
.ind-card h3{font-size:17px;font-weight:700;line-height:26px;margin:12px 0 8px}
.ind-card p{font-size:13px;line-height:23px;color:#dcdcdc}
.blog{left:0;top:3375px;width:1200px;height:630px;background:var(--dark)}
.blog-card{width:330px}
.blog-img{height:215px}
.blog-body{background:var(--white);margin:-30px 22px 0;position:relative;text-align:center;padding:18px 16px 34px}
.blog-body h3{font-size:17px;font-weight:700;line-height:26px;margin-bottom:10px}
.blog-body p{font-size:13px;line-height:26px;color:var(--grey)}
.blog-arrow{position:absolute;left:50%;bottom:-16px;transform:translateX(-50%);width:30px;height:30px;border-radius:50%;background:var(--ink);display:flex;align-items:center;justify-content:center}
.addr{left:75px;top:4075px;width:422px;height:365px;background:var(--dark);border-radius:14px;padding:28px 28px;color:var(--white)}
.addr h2{font-size:42px;font-weight:900;margin-bottom:24px}
.addr-row{display:flex;align-items:center;gap:18px;font-size:15px;line-height:26px;margin-bottom:26px}
.addr-ic{width:50px;height:50px;border-radius:50%;border:1px solid #7a7a7a;display:flex;align-items:center;justify-content:center;flex:none}
.field{position:absolute;background:var(--white);border-radius:26px;box-shadow:0 3px 8px rgba(0,0,0,.16);padding:0 24px;font-size:15px;color:var(--grey);display:flex;align-items:center}
.gov{left:75px;top:4525px;width:1052px;height:265px;background:var(--dark);border-radius:16px}
.gov p{position:absolute;left:30px;top:55px;font-size:33px;line-height:42px;font-weight:900;color:var(--white)}
.badge{position:absolute;top:30px;width:168px;height:208px;background:var(--white)}
.badge-foot{position:absolute;left:0;bottom:0;width:100%;height:58px;background:#1c2a44}
.footer{left:0;top:4790px;width:1200px;height:496px;background:var(--black)}
.fcol h4{font-size:16px;font-weight:900;color:var(--white);margin-bottom:14px}
.fcol a{display:block;font-size:15px;color:var(--white);text-decoration:none;line-height:40px}
.copy{font-size:13px;color:#bdbdbd}
.social{display:flex;gap:18px}
.social span{width:24px;height:24px;border-radius:50%;background:var(--white)}
</style>
</head>
<body>

<!-- Top bar -->
<header class="abs topbar">
  <div class="abs brand" style="left:75px;top:24px"><span class="sq"></span>BRIDGE ON</div>
  <div class="abs contact-chip" style="left:606px;top:22px">
    <span class="chip-ic"><svg width="18" height="18" viewBox="0 0 24 24"><path fill="#1e1e1e" d="M6.6 10.8a15 15 0 0 0 6.6 6.6l2.2-2.2a1 1 0 0 1 1-.25 11.4 11.4 0 0 0 3.6.57 1 1 0 0 1 1 1V20a1 1 0 0 1-1 1A17 17 0 0 1 3 4a1 1 0 0 1 1-1h3.5a1 1 0 0 1 1 1c0 1.25.2 2.45.57 3.57a1 1 0 0 1-.25 1z"/></svg></span>+1 555-014-2730
  </div>
  <div class="abs contact-chip" style="left:850px;top:22px">
    <span class="chip-ic"><svg width="20" height="16" viewBox="0 0 24 18"><rect x="1" y="1" width="22" height="16" rx="2" fill="#1e1e1e"/><path d="M2 2l10 8 10-8" stroke="#fff" stroke-width="2" fill="none"/></svg></span>hello@bridgeon.example
  </div>
</header>

<nav class="abs nav">
  <span>HOME</span><span>ABOUT US</span><span>SERVICES</span><span>INDUSTRY SOLUTIONS</span><span>OUR COMPANY</span><span>LATEST BLOG</span><span>CONTACT US</span>
</nav>

<!-- Hero -->
<section>
  <div class="abs hero" role="img" aria-label="Visitors in a modern audio visual showroom with large illuminated displays"></div>
  <div class="abs hero-shade"></div>
  <h1 class="abs hero" style="background:none;height:auto;width:auto;left:75px;top:325px;font-size:90px;font-weight:900;color:#fff">BRIDGE ON</h1>
  <p class="abs hero-text">Excepteur sint occaecat cupidatat non proidentsunt in culpa qui officia deserunt mollit.</p>
  <span class="abs btn btn-hero">Read More</span>
  <svg class="abs" style="left:0;top:690px" width="1200" height="130" viewBox="0 0 1200 130">
    <path d="M0 80 C300 0 700 130 1200 20 L1200 130 L0 130Z" fill="#8d8d8d"/>
    <path d="M0 100 C300 30 700 140 1200 45 L1200 130 L0 130Z" fill="#ffffff"/>
  </svg>
</section>

<!-- Services -->
<section>
  <h2 class="abs sec" style="left:75px;top:862px">OUR SERVICES</h2>
  <svg class="abs" style="left:1062px;top:878px" width="66" height="22" viewBox="0 0 66 22">
    <path d="M20 11H4M10 4l-7 7 7 7" stroke="#8a8a8a" stroke-width="3" fill="none"/>
    <path d="M44 11h16M54 4l7 7-7 7" stroke="#1e1e1e" stroke-width="3" fill="none"/>
  </svg>
  <div class="abs svc-card" style="left:75px;top:978px;width:330px;height:290px">
    <svg width="70" height="70" viewBox="0 0 70 70" fill="none" stroke="#1e1e1e" stroke-width="2"><rect x="4" y="8" width="40" height="30" rx="2"/><path d="M20 17v12l10-6z"/><rect x="46" y="28" width="12" height="22" rx="6"/><path d="M42 42a10 10 0 0 0 20 0M52 52v10"/></svg>
    <h3>Audio &amp; Visual Design</h3>
    <p>Duis aute irure dolor in rep rehenderit in voluptate velit esse cillum magni do enim ipsam voluptatem quia.</p>
    <span class="btn btn-sm">Read More</span>
  </div>
  <div class="abs svc-card" style="left:435px;top:942px;width:330px;height:290px">
    <svg width="70" height="70" viewBox="0 0 70 70" fill="none" stroke="#1e1e1e" stroke-width="2"><circle cx="35" cy="35" r="18"/><circle cx="35" cy="35" r="26" stroke-dasharray="8 6"/><path d="M26 35l6 6 12-12"/></svg>
    <h3>Audio &amp; Visual Install</h3>
    <p>Duis aute irure dolor in rep rehenderit in voluptate velit esse cillum magni do enim ipsam voluptatem quia.</p>
    <span class="btn btn-sm">Read More</span>
  </div>
  <div class="abs svc-card" style="left:796px;top:978px;width:330px;height:290px">
    <svg width="80" height="70" viewBox="0 0 80 70" fill="none" stroke="#1e1e1e" stroke-width="2"><path d="M38 6h34a4 4 0 0 1 4 4v20a4 4 0 0 1-4 4H56l-8 8v-8h-10a4 4 0 0 1-4-4V10a4 4 0 0 1 4-4z"/><path d="M44 15h26M44 22h26"/><circle cx="24" cy="44" r="20" fill="#fff"/><path d="M18 38a6 6 0 1 1 8 6v4M26 54v1"/></svg>
    <h3>Consulting</h3>
    <p>Duis aute irure dolor in rep rehenderit in voluptate velit esse cillum magni do enim ipsam voluptatem quia.</p>
    <span class="btn btn-sm">Read More</span>
  </div>
</section>

<!-- About -->
<section>
  <svg class="abs" style="left:0;top:1340px" width="1200" height="800" viewBox="0 0 1200 800">
    <path d="M0 60 C250 -20 500 90 800 20 C1000 -20 1120 40 1200 40 L1200 700 C900 760 600 640 300 700 C180 720 80 700 0 720Z" fill="#f2f1f2"/>
    <path d="M0 720 C250 650 500 760 800 690 C1000 650 1120 700 1200 690 L1200 800 L0 800Z" fill="#b3b3b3"/>
    <path d="M0 740 C250 675 500 780 800 710 C1000 670 1120 720 1200 710 L1200 800 L0 800Z" fill="#ffffff"/>
  </svg>
  <h2 class="abs sec" style="left:75px;top:1548px">ABOUT BRIDGEON</h2>
  <p class="abs body-text" style="left:75px;top:1612px;width:430px">Sed ut perspiciatis unde omnis iste natus error sit voluptatem accusantium doloremque laudantium, totam rem aperiam, eaque ipsa quae ab illo inventore veritatis et quasi architecto beatae vitae dicta sunt explicabo. Nemo enim ipsam voluptatem quia voluptas sit aspernatur aut odit aut fugit</p>
  <span class="abs btn" style="left:75px;top:1836px;width:193px;height:52px;font-size:17px">Read More</span>
  <div class="abs photo" style="left:560px;top:1460px;width:500px;height:480px;background:#8f8f8f;transform:rotate(-12deg)"></div>
  <div class="abs photo" style="left:590px;top:1440px;width:500px;height:480px;background:linear-gradient(135deg,#6c6c6c,#c9c9c9 50%,#4a4a4a);transform:rotate(15deg)" role="img" aria-label="Man with glasses working on a laptop"></div>
</section>

<!-- Industry Solutions -->
<section>
  <h2 class="abs sec" style="left:0;top:2200px;width:1200px;text-align:center">INDUSTRY SOLUTIONS</h2>
  <div class="abs ind-card" style="left:75px;top:2287px;width:243px;height:290px">
    <svg width="70" height="66" viewBox="0 0 70 66" fill="none" stroke="#fff" stroke-width="2"><circle cx="35" cy="22" r="9"/><path d="M22 50c0-8 6-14 13-14s13 6 13 14M10 40c0-5 3-8 7-8M60 40c0-5-3-8-7-8M6 62h58"/><circle cx="14" cy="24" r="5"/><circle cx="56" cy="24" r="5"/></svg>
    <h3>IT/Voice Infrastructure Consulting</h3>
    <p>Duis aute irure dolor in rep rehenderit in voluptate velit esse cillum magni do enim ipsam voluptatem quia.</p>
  </div>
  <div class="abs ind-card" style="left:342px;top:2287px;width:241px;height:290px">
    <svg width="70" height="66" viewBox="0 0 70 66" fill="none" stroke="#fff" stroke-width="2"><rect x="8" y="6" width="54" height="38" rx="3"/><path d="M26 58h18M35 44v14"/><circle cx="35" cy="22" r="8"/><path d="M32 30v4h6v-4"/></svg>
    <h3>Design<br>Solutions</h3>
    <p>Duis aute irure dolor in rep rehenderit in voluptate velit esse cillum magni do enim ipsam voluptatem quia.</p>
  </div>
  <div class="abs ind-card" style="left:615px;top:2287px;width:243px;height:290px">
    <svg width="70" height="66" viewBox="0 0 70 66" fill="none" stroke="#fff" stroke-width="2"><rect x="10" y="22" width="50" height="34" rx="2"/><circle cx="35" cy="39" r="9"/><path d="M35 4v10M22 8l4 8M48 8l-4 8M6 62h58"/></svg>
    <h3>Implementation Solutions</h3>
    <p>Duis aute irure dolor in rep rehenderit in voluptate velit esse cillum magni do enim ipsam voluptatem quia.</p>
  </div>
  <div class="abs ind-card" style="left:885px;top:2287px;width:242px;height:290px">
    <svg width="70" height="66" viewBox="0 0 70 66" fill="none" stroke="#fff" stroke-width="2"><rect x="8" y="4" width="54" height="58"/><path d="M8 16h54M20 4v58M32 16v46M44 16v46M8 30h54M8 44h54"/></svg>
    <h3>Project<br>Management</h3>
    <p>Duis aute irure dolor in rep rehenderit in voluptate velit esse cillum magni do enim ipsam voluptatem quia.</p>
  </div>
</section>

<!-- Capabilities -->
<section>
  <svg class="abs" style="left:0;top:2640px" width="1200" height="735" viewBox="0 0 1200 735">
    <path d="M0 70 C250 -10 500 90 800 30 C1000 -10 1120 30 1200 20 L1200 735 L0 735Z" fill="#f2f1f2"/>
  </svg>
  <div class="abs photo" style="left:95px;top:2740px;width:520px;height:500px;background:#8f8f8f;transform:rotate(12deg)"></div>
  <div class="abs photo" style="left:85px;top:2720px;width:520px;height:500px;background:linear-gradient(135deg,#3d3d3d,#d8d8d8 55%,#5a5a5a);transform:rotate(-14deg)" role="img" aria-label="Three colleagues reviewing documents at a meeting table"></div>
  <h2 class="abs sec" style="left:705px;top:2830px">OUR CAPABILITIES</h2>
  <p class="abs body-text" style="left:705px;top:2892px;width:425px">Sed ut perspiciatis unde omnis iste natus error sit voluptatem accusantium doloremque laudantium, totam rem aperiam, eaque ipsa quae ab illo inventore veritatis et quasi architecto beatae vitae dicta sunt explicabo. Nemo enim ipsam voluptatem quia voluptas sit aspernatur aut odit aut fugit</p>
  <span class="abs btn" style="left:705px;top:3115px;width:193px;height:52px;font-size:17px">Read More</span>
</section>

<!-- Blog -->
<section class="abs blog">
  <h2 class="sec" style="position:absolute;left:0;top:75px;width:1200px;text-align:center;color:#fff">LATEST BLOG</h2>
  <div class="abs blog-card" style="left:75px;top:165px">
    <div class="blog-img" style="background:linear-gradient(135deg,#9a9a9a,#e2e2e2 60%,#6e6e6e)" role="img" aria-label="Team meeting around a whiteboard"></div>
    <div class="blog-body"><h3>Neque porro quisquam est quis euismod</h3><p>Nulla nibh justo, tempor nec porta nec, lacinia quis nulla. Cras sit amet vestibulum purus.</p>
      <span class="blog-arrow"><svg width="14" height="12" viewBox="0 0 14 12"><path d="M1 6h11M7 1l5 5-5 5" stroke="#fff" stroke-width="2" fill="none"/></svg></span></div>
  </div>
  <div class="abs blog-card" style="left:435px;top:165px">
    <div class="blog-img" style="background:linear-gradient(160deg,#3a3a3a,#7a6a5a 50%,#2a3848)" role="img" aria-label="Conference room with a large wall screen"></div>
    <div class="blog-body"><h3>Neque porro quisquam est quis euismod</h3><p>Nulla nibh justo, tempor nec porta nec, lacinia quis nulla. Cras sit amet vestibulum purus.</p>
      <span class="blog-arrow"><svg width="14" height="12" viewBox="0 0 14 12"><path d="M1 6h11M7 1l5 5-5 5" stroke="#fff" stroke-width="2" fill="none"/></svg></span></div>
  </div>
  <div class="abs blog-card" style="left:796px;top:165px">
    <div class="blog-img" style="background:linear-gradient(135deg,#d8d8d8,#8a8a8a 55%,#c2c2c2)" role="img" aria-label="Colleagues discussing work at a desk"></div>
    <div class="blog-body"><h3>Neque porro quisquam est quis euismod</h3><p>Nulla nibh justo, tempor nec porta nec, lacinia quis nulla. Cras sit amet vestibulum purus.</p>
      <span class="blog-arrow"><svg width="14" height="12" viewBox="0 0 14 12"><path d="M1 6h11M7 1l5 5-5 5" stroke="#fff" stroke-width="2" fill="none"/></svg></span></div>
  </div>
</section>

<!-- Contact -->
<section>
  <div class="abs addr">
    <h2>ADDRESS INFO</h2>
    <div class="addr-row"><span class="addr-ic"><svg width="18" height="18" viewBox="0 0 24 24"><path fill="#fff" d="M2 5l6-2 8 3 6-2v15l-6 2-8-3-6 2z"/></svg></span>Suite 12/40 Harbor Lane,<br>Eastfield WA 6200</div>
    <div class="addr-row"><span class="addr-ic"><svg width="16" height="16" viewBox="0 0 24 24"><path fill="#fff" d="M6.6 10.8a15 15 0 0 0 6.6 6.6l2.2-2.2a1 1 0 0 1 1-.25 11.4 11.4 0 0 0 3.6.57 1 1 0 0 1 1 1V20a1 1 0 0 1-1 1A17 17 0 0 1 3 4a1 1 0 0 1 1-1h3.5a1 1 0 0 1 1 1c0 1.25.2 2.45.57 3.57a1 1 0 0 1-.25 1z"/></svg></span>+1 555-014-2730</div>
    <div class="addr-row"><span class="addr-ic"><svg width="18" height="14" viewBox="0 0 24 18"><rect x="1" y="1" width="22" height="16" rx="2" fill="#fff"/><path d="M2 2l10 8 10-8" stroke="#2b2b2b" stroke-width="2" fill="none"/></svg></span>hello@bridgeon.example</div>
  </div>
  <h2 class="abs sec" style="left:523px;top:4072px">CONTACT US</h2>
  <div class="field" style="left:523px;top:4145px;width:300px;height:52px">Name</div>
  <div class="field" style="left:835px;top:4145px;width:292px;height:52px">Phone No</div>
  <div class="field" style="left:523px;top:4215px;width:604px;height:52px">Email Address</div>
  <div class="field" style="left:523px;top:4285px;width:604px;height:90px;align-items:flex-start;padding-top:22px">Message</div>
  <span class="abs btn" style="left:523px;top:4382px;width:210px;height:56px;font-size:23px;background:#3d3d3d">Send</span>
</section>

<!-- Government banner -->
<svg class="abs" style="left:0;top:4690px" width="1200" height="110" viewBox="0 0 1200 110">
  <path d="M0 55 C300 -10 800 60 1200 0 L1200 110 L0 110Z" fill="#9a9a9a"/>
  <path d="M0 80 C300 15 800 85 1200 25 L1200 110 L0 110Z" fill="#0d0d0d"/>
</svg>
<section class="abs gov">
  <p>WE WILL BE SPECIALIZING IN<br>GOVERNMENT CONTRACTING FOR<br>SDVOSB SET ASIDE AND SOLE<br>SOURCE CONTRACTS.</p>
  <div class="badge" style="left:622px"><div class="badge-foot"></div></div>
  <div class="badge" style="left:817px"><div class="badge-foot"></div></div>
</section>

<!-- Footer -->
<footer class="abs footer">
  <div class="abs brand" style="left:75px;top:178px;color:#fff"><span class="sq" style="background:#fff"></span>BRIDGE ON</div>
  <div class="abs fcol" style="left:362px;top:80px"><h4>SITE MAP</h4><a>Home</a><a>About Us</a><a>Services</a><a>Industry Solutions</a><a>Our Company</a><a>Contact Us</a></div>
  <div class="abs fcol" style="left:598px;top:80px"><h4>SERVICES</h4><a>Audio &amp; Visual Design</a><a>Install</a><a>Consulting</a></div>
  <div class="abs fcol" style="left:855px;top:80px"><h4>INDUSTRY SOLUTIONS</h4><a>IT/Voice Infrastructure Consulting</a><a>Design</a><a>Implementation</a><a>Project Management</a></div>
  <div class="abs" style="left:0;top:410px;width:1200px;height:1px;background:#2a2a2a"></div>
  <p class="abs copy" style="left:75px;top:438px">Copyright © 2024 bRIDGE ON LLC All Rights Reserved.</p>
  <div class="abs social" style="left:932px;top:432px"><span></span><span></span><span></span><span></span><span></span></div>
</footer>

</body>
</html>
```